Tarvex Engineering Rail Sector Brochure

We need a new 3 page folding brochure for Tarvex Engineering Pty Ltd. The organisation is currently supporting customers in Defence, Maritime and Information and Communications Technology companies. We are currently looking to expand our engineering services into the rail sector by providing manpower and consultancy services to railway sector clients.We would like the brochure to be based on an A4 page and look technical with particular focus on communications systems used within the railways. This could include pictures of rail control centres, trains (Australian trains only please), train radio communications equipment, radio antennas, computers and networking equipment. Please use both graphics and photos.The brochure will be provided to potential rail customers and should be clear and uncluttered.The following is our company website: www.tarvexengineering.com.au if you would like more detail on our current work.I have attached the file for our logo which should appear on the brochure.
Target Market(s)
Providing manpower and consultancy services to the railway sector. This includes rail companies (e.g. Quillane Transit Lines, K/Rail etc) and rail equipment and carriage suppliers (e.g. Feltmark)
Colors
Designer to choose colors to be used in the design.
Requirements
Must have
- Instead of having "lorem ipsum" text in the brochure you can please use some of the text in the file we have provided. Not all has to be used, and you should not be limited to what is in the file.
Nice to have
- Mixture of different font sizes to highlight particular text elements.

```html
<!DOCTYPE html>
<html lang="en">
<head>
<meta charset="utf-8">
<title>Tarvex Engineering Rail Sector Brochure</title>
<link href="https://fonts.googleapis.com/css2?family=Open+Sans:wght@400;600;700;800&display=swap" rel="stylesheet">
<style>
  :root {
    --stage: #555555;
    --paper: #f1f1f2;
    --paper-shade: #e4e4e6;
    --edge: #2a2a2c;
    --blue: #1f4fb8;
    --blue-deep: #0a2a8c;
    --blue-head: #2553c4;
    --ink: #1d1d28;
    --ring-track: #3a3a3a;
    --ring-green: #1db36b;
    --ring-teal: #17a2c4;
    --ring-gold: #c9a400;
  }
  * { box-sizing: border-box; margin: 0; padding: 0; }
  html, body { width: 1200px; height: 800px; overflow: hidden; background: var(--stage); }
  body { font-family: "Open Sans", sans-serif; color: var(--ink); }

  .brochure {
    position: absolute; left: 60px; top: 18px;
    width: 1080px; height: 764px;
    background: linear-gradient(90deg, var(--paper) 0%, var(--paper) 31%, var(--paper-shade) 33.3%, var(--paper) 36%, var(--paper) 64%, var(--paper-shade) 66.6%, var(--paper) 69%);
    overflow: hidden;
  }
  .brochure-art { position: absolute; inset: 0; }

  .section { position: absolute; }
  .section-title { font-size: 22px; font-weight: 700; line-height: 1.2; color: var(--ink); }
  .section-title .accent { color: var(--blue-head); }
  .section-rule { width: 30px; height: 6px; border-radius: 3px; background: var(--ink); margin: 10px 0 12px; }
  .tick-list { list-style: none; font-size: 13px; line-height: 1.55; }
  .tick-list li { padding-left: 16px; position: relative; }
  .tick-list li::before { content: "\2713"; position: absolute; left: 0; color: var(--blue-head); font-weight: 700; }

  .network { left: 36px; top: 58px; width: 300px; }
  .comms { left: 396px; top: 58px; width: 300px; }
  .command { left: 396px; top: 300px; width: 300px; }
  .sensor { left: 756px; top: 200px; width: 300px; }

  .cover-title {
    position: absolute; left: 40px; top: 590px;
    color: #fff; font-size: 40px; font-weight: 800; line-height: 1.05; letter-spacing: 1px;
  }
  .cover-tagline {
    position: absolute; left: 42px; top: 690px;
    color: #fff; font-size: 17px; font-weight: 600; line-height: 1.3;
  }
</style>
</head>
<body>
<main class="brochure">
  <svg class="brochure-art" viewBox="0 0 1080 764" width="1080" height="764" aria-hidden="false">
    <defs>
      <linearGradient id="bandPhoto" x1="0" y1="0" x2="1" y2="1">
        <stop offset="0" stop-color="#1b3f9a"/>
        <stop offset="0.5" stop-color="#2356c4"/>
        <stop offset="1" stop-color="#1a46a8"/>
      </linearGradient>
      <linearGradient id="skyPhoto" x1="0" y1="0" x2="1" y2="1">
        <stop offset="0" stop-color="#0a238a"/>
        <stop offset="1" stop-color="#1f4fb8"/>
      </linearGradient>
      <linearGradient id="deskPhoto" x1="0" y1="0" x2="1" y2="1">
        <stop offset="0" stop-color="#3b3833"/>
        <stop offset="0.6" stop-color="#6d7378"/>
        <stop offset="1" stop-color="#a7b3c0"/>
      </linearGradient>
      <linearGradient id="consolePhoto" x1="0" y1="0" x2="1" y2="1">
        <stop offset="0" stop-color="#4a5560"/>
        <stop offset="0.6" stop-color="#3c6e86"/>
        <stop offset="1" stop-color="#1d2a3a"/>
      </linearGradient>
      <linearGradient id="towerPhoto" x1="0" y1="0" x2="1" y2="1">
        <stop offset="0" stop-color="#3a5fae"/>
        <stop offset="0.5" stop-color="#b59a78"/>
        <stop offset="1" stop-color="#2c4b94"/>
      </linearGradient>
    </defs>

    <!-- top edge strip -->
    <rect x="0" y="0" width="720" height="14" fill="var(--edge)"/>
    <rect x="0" y="0" width="14" height="480" fill="var(--edge)"/>

    <!-- top right header -->
    <path d="M690 0 L1080 0 L1080 150 C980 118 850 138 720 205 L720 60 C712 40 700 20 690 0 Z" fill="url(#skyPhoto)" role="img" aria-label="Photo of a satellite dish antenna against a blue sky"/>

    <!-- bottom blue band -->
    <path d="M0 450 C120 430 250 470 330 540 C420 620 560 625 720 600 C860 580 960 555 1080 520 L1080 764 L0 764 Z" fill="url(#bandPhoto)" role="img" aria-label="Blue-toned photo of railway signal lights beside the track"/>

    <!-- photos -->
    <rect x="34" y="300" width="290" height="160" fill="url(#deskPhoto)" role="img" aria-label="Photo of a train driver's control desk"/>
    <rect x="430" y="552" width="260" height="168" fill="url(#consolePhoto)" role="img" aria-label="Photo of an operator using a rail control console"/>
    <rect x="430" y="552" width="260" height="168" fill="none" stroke="#ffffff" stroke-width="1.5"/>
    <rect x="770" y="510" width="280" height="190" fill="url(#towerPhoto)" role="img" aria-label="Photo of an office building under a blue sky"/>
    <rect x="776" y="516" width="268" height="178" fill="none" stroke="#ffffff" stroke-width="1.2"/>

    <!-- rings -->
    <g font-family="Open Sans, sans-serif" font-size="7" font-weight="700" text-anchor="middle" fill="#1d1d28">
      <circle cx="810" cy="440" r="32" fill="none" stroke="var(--ring-track)" stroke-width="7"/>
      <circle cx="810" cy="440" r="32" fill="none" stroke="var(--ring-green)" stroke-width="7" stroke-dasharray="183 201" transform="rotate(-90 810 440)"/>
      <text x="810" y="438">PERFORMANCE</text><text x="810" y="448">91%</text>
      <circle cx="895" cy="410" r="32" fill="none" stroke="var(--ring-track)" stroke-width="7"/>
      <circle cx="895" cy="410" r="32" fill="none" stroke="var(--ring-teal)" stroke-width="7" stroke-dasharray="177 201" transform="rotate(-90 895 410)"/>
      <text x="895" y="408">VALUE</text><text x="895" y="418">88%</text>
      <circle cx="980" cy="380" r="32" fill="none" stroke="var(--ring-track)" stroke-width="7"/>
      <circle cx="980" cy="380" r="32" fill="none" stroke="var(--ring-gold)" stroke-width="7" stroke-dasharray="191 201" transform="rotate(-90 980 380)"/>
      <text x="980" y="378">QUALITY</text><text x="980" y="388">95%</text>
    </g>
  </svg>

  <section class="section network">
    <h2 class="section-title"><span class="accent">Network</span> Systems <span class="accent">– 40%</span></h2>
    <div class="section-rule"></div>
    <ul class="tick-list">
      <li>Defence Classified Networking</li>
      <li>Cryptographic Systems design</li>
      <li>High Speed Data Communications</li>
      <li>IP Voice Communications Systems Integration</li>
      <li>Information and Cybersecurity solutions</li>
    </ul>
  </section>

  <section class="section comms">
    <h2 class="section-title"><span class="accent">Communications</span><br>Systems <span class="accent">– 35%</span></h2>
    <div class="section-rule"></div>
    <ul class="tick-list">
      <li>Secure communications architecture</li>
      <li>Wideband Data Links and WIFI</li>
      <li>Microwave and Satellite Communications</li>
      <li>Custom/Speciality Antennas and RF Systems</li>
      <li>Anti-Jam Communications links</li>
    </ul>
  </section>

  <section class="section command">
    <h2 class="section-title"><span class="accent">Command and<br>Control</span> Systems <span class="accent">– 20%</span></h2>
    <div class="section-rule"></div>
    <ul class="tick-list">
      <li>Human Factors design and development</li>
      <li>Command System integration</li>
      <li>UHD TV and Video Wall display design</li>
      <li>C2 Network integration</li>
    </ul>
  </section>

  <section class="section sensor">
    <h2 class="section-title"><span class="accent">Sensor</span> Systems <span class="accent">– 5%</span></h2>
    <div class="section-rule"></div>
    <ul class="tick-list">
      <li>Thermal monitoring</li>
      <li>Data Logging and Analysis</li>
      <li>IoT Sensor integration</li>
      <li>Shock/Vibration and Acoustics inspection and test services</li>
    </ul>
  </section>

  <h1 class="cover-title">ENGINEERING<br>SERVICES</h1>
  <p class="cover-tagline">Smart solutions<br>that deliver Excellence</p>
</main>
</body>
</html>
```